Broschüre für Personaldienstleister
Zielgruppe
Wir sind ein Personaldienstleister und vermitteln ausländisches medizinisches Fachpersonal an deutsche Einrichtungen. Unsere Zielgruppe sind Krankenhäuser, Pflegeheime, Ärztehäuser, Praxen, Labore und weitere medizinische Institutionen.
Aufgabenstellung
Wir haben eine Infobroschüre sowie eine PowerPoint Präsentation bereits mit einem groben Design erstellt. Texte und Beispielbilder (Stockmaterial) sind ebenfalls vorhanden, gerne wünschen wir uns auch Eigeninitiative bei der Wahl der Bilder passend zum neuen Design.
Wir wünschen uns ein Redesign mit einem kreativen, einzigartigen Design. Zudem ist uns wichtig, dass unsere Infografiken qualitativ und hochwertig gestaltet werden.
Dieses Projekt ist mit zukünftigen Folgeprojekten verbunden, da wir weitere Präsentationen und Broschüren für andere Zielgruppen benötigen.

```html
<!DOCTYPE html>
<html lang="de">
<head>
<meta charset="utf-8">
<title>Veltoria HR – Fachpersonal aus der Türkei</title>
<link href="https://fonts.googleapis.com/css2?family=Roboto:wght@400;500;700;900&family=Fira+Sans:wght@400;500;600&display=swap" rel="stylesheet">
<style>
:root{
  --teal-dark:#1b4249;
  --teal-mid:#3a8a6b;
  --mint:#cfe7de;
  --ink:#1b4249;
  --grey-text:#4c4c4c;
  --dash:#9a9a9a;
  --frame:#6e6e6e;
  --white:#ffffff;
}
*{margin:0;padding:0;box-sizing:border-box}
html,body{width:1200px;height:833px;overflow:hidden;background:var(--frame)}
.canvas{position:relative;width:1200px;height:833px;font-family:"Roboto",sans-serif;color:var(--grey-text)}
.page{position:absolute;top:8px;height:817px;background:var(--white)}
.page--left{left:5px;width:591px}
.page--right{left:600px;width:592px}
.shapes{position:absolute;left:0;top:0}
.hero{position:absolute;left:12px;top:13px;width:578px;height:323px;background:var(--teal-dark)}
.hero__title{position:absolute;left:41px;top:68px;font:700 32.5px/39px "Roboto",sans-serif;color:var(--white);letter-spacing:.2px}
.hero__photo{position:absolute;left:355px;top:47px;width:225px;height:289px;background:linear-gradient(180deg,#3e6b6f 0%,#2f86c9 55%,#2a7cc0 100%);border-radius:90px 90px 0 0}
.section-title{position:absolute;font-family:"Fira Sans",sans-serif;font-weight:500;color:var(--ink);text-align:center}
.section-title--left{left:12px;width:578px;top:356px;font-size:26px;line-height:31px}
.section-title--right{left:600px;width:592px;top:48px;font-size:23.5px;line-height:27px}
.pill{position:absolute;width:194px;height:68px;border-radius:34px}
.pill--dark{background:var(--teal-dark);color:var(--white)}
.pill--mint{background:var(--mint);color:var(--teal-dark)}
.pill--green{background:var(--teal-mid);color:var(--white)}
.pill__text{position:absolute;top:7px;width:113px}
.pill--l .pill__text{left:20px}
.pill--r .pill__text{left:62px}
.pill__title{font-weight:500;font-size:7.6px;line-height:9px;margin-bottom:2px}
.pill__body{font-size:5.5px;line-height:6.6px;text-align:justify}
.footer{position:absolute;top:796px;height:25px;background:var(--teal-dark);color:var(--white);font-size:10px}
.footer span{position:absolute;top:6px;transform:translateX(-50%);white-space:nowrap}
.footer--left{left:11px;width:579px}
.footer--right{left:606px;width:580px}
.benefit{position:absolute;color:var(--grey-text)}
.benefit__title{font-family:"Roboto",sans-serif;font-weight:500;font-size:8.6px;line-height:10.4px;color:var(--teal-dark);margin-bottom:4px}
.benefit__body{font-size:6.6px;line-height:8px;text-align:justify}
.benefit--center .benefit__body{text-align:center}
.brand{position:absolute;left:812px;top:364px;width:166px;text-align:center;font:700 20px/24px "Roboto",sans-serif;color:var(--teal-dark);letter-spacing:.3px}
.hub-label{position:absolute;left:262px;top:591px;width:68px;text-align:center;font:700 9px/11px "Roboto",sans-serif;color:var(--white)}
</style>
</head>
<body>
<div class="canvas">
  <section class="page page--left"></section>
  <section class="page page--right"></section>

  <div class="hero">
    <h1 class="hero__title">QUALIFIZIERTES<br>FACHPERSONAL<br>AUS DER TÜRKEI</h1>
  </div>
  <div class="hero__photo" style="left:355px;top:47px" role="img" aria-label="Foto einer lächelnden Pflegefachkraft in blauer Berufskleidung, die zur Überschrift zeigt"></div>

  <h2 class="section-title section-title--left">Die Türkei bietet gegenüber anderen<br>Drittstaaten viele Vorteile</h2>
  <h2 class="section-title section-title--right">Genießen Sie weitere Vorteile, wenn Sie uns mit der<br>Rekrutierung neuer Fachkräfte beauftragen.</h2>

  <svg class="shapes" width="1200" height="833" viewBox="0 0 1200 833" aria-hidden="true">
    <!-- left infographic connectors -->
    <g fill="none" stroke="#9aa" stroke-width=".7" stroke-dasharray="1 1.5">
      <polyline points="234,493 259,493 283,536"/>
      <polyline points="364,493 340,493 311,536"/>
      <polyline points="224,595 234,595"/>
      <polyline points="363,596 376,596"/>
      <polyline points="224,695 264,695 284,660"/>
      <polyline points="381,695 343,695 318,659"/>
      <circle cx="296" cy="598" r="58"/>
    </g>
    <g fill="var(--white)" stroke="var(--teal-dark)" stroke-width="1.2">
      <circle cx="285" cy="542" r="6"/><circle cx="310" cy="543" r="6"/>
    </g>
    <g fill="var(--teal-dark)"><circle cx="285" cy="542" r="2"/><circle cx="310" cy="543" r="2"/></g>
    <g fill="var(--white)" stroke="var(--mint)" stroke-width="1.2">
      <circle cx="240" cy="595" r="6"/><circle cx="357" cy="596" r="6"/>
    </g>
    <g fill="var(--mint)"><circle cx="240" cy="595" r="2"/><circle cx="357" cy="596" r="2"/></g>
    <g fill="var(--white)" stroke="var(--teal-mid)" stroke-width="1.2">
      <circle cx="285" cy="655" r="6"/><circle cx="317" cy="654" r="6"/>
    </g>
    <g fill="var(--teal-mid)"><circle cx="285" cy="655" r="2"/><circle cx="317" cy="654" r="2"/></g>
    <circle cx="296" cy="598" r="34" fill="var(--teal-dark)" stroke="var(--mint)" stroke-width="3"/>

    <!-- right page dashed frames -->
    <g fill="none" stroke="var(--dash)" stroke-width=".8" stroke-dasharray="3 2">
      <path d="M674,222 V197 a20,20 0 0 1 20,-20 H856 a20,20 0 0 1 20,20 V286"/>
      <path d="M922,286 V197 a20,20 0 0 1 20,-20 H1112 a20,20 0 0 1 20,20 V222"/>
      <path d="M645,316 V293 a20,20 0 0 1 20,-20 H821 a20,20 0 0 1 20,20 V310 M645,352 V396 M645,433 V457 a20,20 0 0 0 20,20 H821 a20,20 0 0 0 22,-27"/>
      <path d="M945,300 V293 a20,20 0 0 1 20,-20 H1127 a20,20 0 0 1 20,20 V322 M1147,362 V390 M1147,430 V457 a20,20 0 0 1 -20,20 H965 a20,20 0 0 1 -20,-20 V450"/>
      <path d="M673,527 V557 a20,20 0 0 0 20,20 H855 a20,20 0 0 0 20,-20 V477"/>
      <path d="M919,477 V557 a20,20 0 0 0 20,20 H1102 a20,20 0 0 0 20,-20 V533"/>
      <path d="M794,662 V612 a20,20 0 0 1 20,-20 H873 M917,592 H976 a20,20 0 0 1 20,20 V662"/>
      <path d="M895,484 V568"/>
    </g>
    <polygon points="895,287 976,334 976,426 895,473 814,426 814,334" fill="none" stroke="var(--teal-dark)" stroke-width="6" stroke-linejoin="miter"/>

    <!-- hexagon icon badges -->
    <g fill="var(--teal-dark)">
      <polygon points="673,219 691,229.5 691,250.5 673,261 655,250.5 655,229.5"/>
      <polygon points="1131,219 1149,229.5 1149,250.5 1131,261 1113,250.5 1113,229.5"/>
      <polygon points="645,313 663,323.5 663,344.5 645,355 627,344.5 627,323.5"/>
      <polygon points="1147,321 1165,331.5 1165,352.5 1147,363 1129,352.5 1129,331.5"/>
      <polygon points="641,392 659,402.5 659,423.5 641,434 623,423.5 623,402.5"/>
      <polygon points="1146,388 1164,398.5 1164,419.5 1146,430 1128,419.5 1128,398.5"/>
      <polygon points="673,486 691,496.5 691,517.5 673,528 655,517.5 655,496.5"/>
      <polygon points="1122,492 1140,502.5 1140,523.5 1122,534 1104,523.5 1104,502.5"/>
      <polygon points="895,568 913,578.5 913,599.5 895,610 877,599.5 877,578.5"/>
    </g>
    <!-- simple white glyphs -->
    <g fill="none" stroke="var(--white)" stroke-width="1.1" stroke-linecap="round">
      <circle cx="668" cy="236" r="3"/><circle cx="678" cy="236" r="3"/><path d="M662,247 a6,6 0 0 1 12,0 M672,247 a6,6 0 0 1 12,0"/>
      <path d="M1128,232 a7,7 0 1 0 4,13 v4 M1135,230 v6 M1132,233 h6"/>
      <circle cx="645" cy="334" r="9"/><path d="M645,328 v6 h-4"/>
      <circle cx="1147" cy="338" r="2.5"/><path d="M1147,341 v8 M1142,337 l5,4 5,-4 M1144,352 h6"/>
      <path d="M634,420 l10,-10 q4,-4 6,-4 q0,2 -4,6 l-10,10 z M636,414 h-3 M639,424 v3"/>
      <circle cx="1146" cy="404" r="3"/><path d="M1140,414 a6,6 0 0 1 12,0 M1139,420 h14"/>
      <circle cx="673" cy="507" r="9"/><path d="M664,507 h18 M673,498 q-5,9 0,18 q5,-9 0,-18"/>
      <path d="M1114,522 h16 M1117,522 v-5 M1122,522 v-8 M1127,522 v-11 M1118,510 l4,-3"/>
      <path d="M887,581 h16 v16 h-16 z M895,581 v16 M887,589 h16"/>
    </g>
    <!-- left pill icon circles -->
    <g fill="var(--white)">
      <circle cx="193" cy="494" r="24"/>
      <circle cx="408" cy="496" r="24"/>
      <circle cx="193" cy="582" r="24"/>
      <circle cx="408" cy="582" r="24"/>
      <circle cx="193" cy="668" r="24"/>
      <circle cx="408" cy="668" r="24"/>
    </g>
  </svg>

  <!-- left infographic pills -->
  <div class="pill pill--dark pill--l" style="left:29px;top:460px">
    <div class="pill__text"><p class="pill__title">Geografische &amp; politische Nähe</p><p class="pill__body">Reisebarrieren sind deutlich niedriger für Personen aus der Türkei als bspw. für Fachkräfte von den Philippinen. Zudem besteht als europäisches Land und EU-Beitrittskandidat ein hohes Maß an rechtlicher Kohärenz mit der EU.</p></div>
  </div>
  <div class="pill pill--dark pill--r" style="left:377px;top:462px">
    <div class="pill__text"><p class="pill__title">Hohe Ausbildungsqualität</p><p class="pill__body">Die Ausbildungsstandards im türkischen Gesundheitswesen liegen im internationalen Vergleich auf einem hohen Niveau.</p></div>
  </div>
  <div class="pill pill--mint pill--l" style="left:29px;top:548px">
    <div class="pill__text"><p class="pill__title">Kulturelle Akzeptanz</p><p class="pill__body">Deutschland ist seit vielen Jahrzehnten ein beliebtes Einwanderungsland für türkischstämmige Mitmenschen. Die gesellschaftliche Akzeptanz in unserem Land ist dementsprechend deutlich höher.</p></div>
  </div>
  <div class="pill pill--mint pill--r" style="left:377px;top:548px">
    <div class="pill__text"><p class="pill__title">Analoges<br>Gesundheitssystem</p><p class="pill__body">Das Gesundheitssystem der Türkei ist dem von Deutschland sehr ähnlich. Missverständnisse und Irrtümer lassen sich dadurch auf ein Minimum reduzieren.</p></div>
  </div>
  <div class="pill pill--green pill--l" style="left:29px;top:634px">
    <div class="pill__text"><p class="pill__title">Leichtere Integration</p><p class="pill__body">Aufgrund der türkischen Community in Deutschland und der damit verbundenen guten Infrastruktur, verläuft die Integration von türkischen Fachkräften deutlich einfacher und schneller.</p></div>
  </div>
  <div class="pill pill--green pill--r" style="left:377px;top:634px">
    <div class="pill__text"><p class="pill__title">Qualifiziert &amp; motiviert</p><p class="pill__body">Türkisches Fachpersonal ist nicht nur ausreichend für den deutschen Arbeitsmarkt qualifiziert, sie sind zudem äußerst motiviert und engagiert mit Hinblick auf eine berufliche Perspektive in Deutschland.</p></div>
  </div>

  <svg class="shapes" width="1200" height="833" viewBox="0 0 1200 833" aria-hidden="true">
    <g fill="none" stroke-width="1.4" stroke-linecap="round" stroke-linejoin="round">
      <path d="M193,507 c-8,-10 -10,-14 -10,-18 a10,10 0 0 1 20,0 c0,4 -2,8 -10,18 z" fill="var(--teal-dark)"/>
      <circle cx="193" cy="489" r="3.5" fill="var(--white)" stroke="none"/>
      <path d="M396,486 h22 v14 h-22 z M402,505 h12" stroke="var(--teal-dark)"/>
      <path d="M182,582 l6,-6 6,3 6,-3 6,6 -8,8 -8,-4 z" stroke="#9cc9b8"/>
      <circle cx="404" cy="574" r="3" stroke="#9cc9b8"/><path d="M404,578 v12 M398,584 h12 M401,596 l3,-6 3,6" stroke="#9cc9b8"/>
      <path d="M183,658 h20 v20 h-20 z M193,658 v20 M183,668 h20" stroke="var(--teal-mid)"/>
      <circle cx="404" cy="660" r="4" stroke="var(--teal-mid)"/><path d="M397,676 a7,7 0 0 1 12,-6 M411,672 l1.5,3 3,.3 -2.2,2 .6,3 -2.9,-1.5 -2.9,1.5 .6,-3 -2.2,-2 3,-.3 z" stroke="var(--teal-mid)"/>
    </g>
  </svg>
  <div class="hub-label">Veltoria HR</div>

  <!-- right page benefits -->
  <div class="brand">Veltoria HR</div>

  <div class="benefit" style="left:699px;top:189px;width:144px">
    <p class="benefit__title">Vergrößerter Kreis potenzieller<br>Bewerber:innen</p>
    <p class="benefit__body">Ein großer Bewerberpool erleichtert es Ihnen, Stellen mit hochqualifizierten Personal zu besetzen, die sonst vakant bleiben würden.</p>
  </div>
  <div class="benefit" style="left:946px;top:189px;width:152px">
    <p class="benefit__title">Verbesserte Patientenorientierung</p>
    <p class="benefit__body">Mit einer vielfältigen Belegschaft können Sie die individuellen Bedürfnisse Ihrer Patienten:innen besser bedienen. Gerade Patienten:innen mit Migrationshintergrund werden es zu schätzen wissen, wenn sich Ihre Mitarbeiter:innen mit der Sprache und den kulturellen Besonderheiten anderer Länder auskennen.</p>
  </div>
  <div class="benefit" style="left:669px;top:283px;width:129px">
    <p class="benefit__title">Hohe Zeit- und<br>Aufwandersparnis</p>
    <p class="benefit__body">Unser 360°-Service ermöglicht es Ihnen, sich voll und ganz den wichtigen Angelegenheiten im Gesundheitswesen zu widmen.</p>
  </div>
  <div class="benefit" style="left:993px;top:283px;width:128px">
    <p class="benefit__title">Nachhaltiger Erfolg</p>
    <p class="benefit__body">Durch unsere umfassende Betreuung bis zum Ende der Probezeit und darüber hinaus, wird sichergestellt, dass sich Ihre neuen Mitarbeiter:innen gut integriert und angekommen fühlen - ein wichtiger Meilenstein auf dem Weg zu nachhaltigem Erfolg.</p>
  </div>
  <div class="benefit" style="left:669px;top:398px;width:128px">
    <p class="benefit__title">Gesteigerte Innovationskraft</p>
    <p class="benefit__body">Durch Mitarbeiter.innen unterschiedlicher Nationalitäten fördern Sie kreative Prozesse und erhöhen die internationale und interkulturelle Kompetenz Ihrer Einrichtung. Hierdurch werden neue Perspektiven und Denkweisen eröffnet.</p>
  </div>
  <div class="benefit" style="left:993px;top:401px;width:127px">
    <p class="benefit__title">Motivierte Mitarbeiter:innen</p>
    <p class="benefit__body">Fachkräfte, die zum Arbeiten ins Ausland aufbrechen, haben eine spürbar höhere Arbeits- und Erfolgsmotivation und gehen häufig mit mehr Engagement und Leidenschaft an bestimmte Aufgaben heran.</p>
  </div>
  <div class="benefit" style="left:704px;top:493px;width:152px">
    <p class="benefit__title">Gesteigerte<br>Internationalisierung</p>
    <p class="benefit__body">Die Beschäftigung von Fachkräften aus dem Ausland erhöht die internationale und interkulturelle Kompetenz Ihrer Einrichtung. Sprachliche und kulturelle Landeskenntnisse Ihres internationalen Personals bieten zudem einen enormen Vorteil im nationalen Wettbewerbsvergleich.</p>
  </div>
  <div class="benefit" style="left:935px;top:498px;width:164px">
    <p class="benefit__title" style="margin-bottom:9px">Verbessertes Unternehmensimage</p>
    <p class="benefit__body">Viele Arbeitnehmer:innen erwarten heute weltoffene Arbeitgeber:innen. Mit einem internationalen Mitarbeiterstab können Sie Ihre Arbeitgeberattraktivität steigern und Ihr Image als moderne Einrichtung unterstreichen.</p>
  </div>
  <div class="benefit benefit--center" style="left:815px;top:619px;width:160px;text-align:center">
    <p class="benefit__title">Gestärkte Vielfalt</p>
    <p class="benefit__body">Eine vielfältige Belegschaft bringt unterschiedliches Wissen, Sichtweisen und Erfahrungen zusammen. Ein „Bunt“ zusammengesetztes Personal kann voneinander lernen und so ihre jeweiligen Stärken kombinieren.</p>
  </div>

  <footer class="footer footer--left">
    <span style="left:108px">+49 000 555 12 345</span>
    <span style="left:294px">hr@veltoria-hr.com</span>
    <span style="left:467px">www.veltoria-hr.com</span>
  </footer>
  <footer class="footer footer--right">
    <span style="left:108px">+49 000 555 12 345</span>
    <span style="left:294px">hr@veltoria-hr.com</span>
    <span style="left:467px">www.veltoria-hr.com</span>
  </footer>
</div>
</body>
</html>
```